Website design for Puddle Jump Kidscare

I need a website designed for my daycare business, Puddle Jump Kidscare, now that I have a new logo. My former website was ok but simple and I did not have a logo yet. It also was created by me using a template and was entirely pink. I loved the bright, happy feel of it but worried it might not appeal as much to potential clients who have sons. Therefore, I need a site which will appeal to both genders while still keeping the cheerful color scheme of my new logo, which has pinks, blue, green and cream.
Updates

Reason: Hello! I am still trying to download my new logo and am sorry it is taking me so long. Hopefully I will it posted by the end of today (US Eastern Standard Time). Thank you all very much for your patience!

Hello! I have finally managed to upload my new logo for you to use in designing my website. I'm sorry it took so long and greatly appreciate your time and creative efforts! I look forward to seeing what is submitted based on my logo design and its style/colors.

Many thanks!

Reason: As I've been traveling and posted my logo file late, I am extending my deadline. I am now back and can focus on providing more and better feedback. I appreciate your patience and submissions very much!

Reason: I need more time to provide feedback and make decisions.

Industry/Entity Type

Daycare

Colors
0192cd
33a6d7
86cae7
cadf82
fbf289
add136
e34197

```html
<!DOCTYPE html>
<html lang="en">
<head>
<meta charset="utf-8">
<title>Puddle Jump Kidscare</title>
<link rel="stylesheet" href="https://fonts.googleapis.com/css2?family=Open+Sans:wght@400;600&family=Sniglet:wght@400;800&display=swap">
<style>
:root{
  --blue:#0192cd;
  --blue-mid:#33a6d7;
  --blue-light:#86cae7;
  --green:#add136;
  --green-light:#cadf82;
  --yellow:#fbf289;
  --pink:#e34197;
  --pink-deep:#c5416f;
  --cream:#fffbea;
  --brown:#6b5526;
  --text:#8a8a8a;
  --white:#ffffff;
}
*{box-sizing:border-box;margin:0;padding:0}
html,body{width:940px;height:1200px;overflow:hidden;background:var(--white)}
body{font-family:"Open Sans",sans-serif;color:var(--text);position:relative}

.site-header{position:absolute;left:0;top:0;width:940px;height:136px;background:linear-gradient(var(--white) 70%,var(--cream))}
.brand{position:absolute;left:86px;top:48px;display:flex;align-items:center;gap:10px}
.brand-dot{width:34px;height:34px;border-radius:50%;background:var(--green)}
.brand-name{font-size:22px;font-weight:600;color:var(--pink-deep)}
.search{position:absolute;left:682px;top:20px;width:172px;height:43px;border:1px solid #e3e3e3;background:var(--white);display:flex;align-items:center;padding-left:13px;gap:8px;font-size:10px;font-weight:600;color:#cfcfcf}

.main-nav{position:absolute;left:0;top:136px;width:940px;height:52px;background:linear-gradient(var(--blue-mid),var(--blue))}
.main-nav a{position:absolute;top:0;height:52px;line-height:52px;color:var(--white);font-size:11.5px;font-weight:600;text-decoration:none}
.main-nav a.active{background:linear-gradient(var(--green),#8fb526);width:49px;text-align:center}

.hero{position:absolute;left:0;top:188px;width:940px;height:320px;background:linear-gradient(100deg,#5e6b45 0%,#6f6a4a 40%,#3f4a55 62%,#6e6556 80%,#8b8170 100%)}
.hero-caption{position:absolute;left:85px;top:77px;width:392px;height:162px;background:rgba(60,65,50,.55);padding:2px 11px;font-family:"Sniglet",cursive;color:var(--white)}
.hero-caption .lead{font-size:23px;line-height:38px;font-weight:400}
.hero-caption .big{font-size:46px;line-height:58px;font-weight:800}
.hero-caption .big2{font-size:37px;line-height:56px;font-weight:800;white-space:nowrap}
.hero-arrow{position:absolute;top:152px;width:32px;height:32px;border-radius:50%;background:var(--white);display:flex;align-items:center;justify-content:center}
.hero-shadow{position:absolute;left:86px;top:508px;width:768px;height:14px;background:radial-gradient(ellipse at top,rgba(0,0,0,.18),rgba(0,0,0,0) 70%)}

.welcome-photo{position:absolute;left:64px;top:544px;width:263px;height:198px;background:radial-gradient(circle at 50% 50%,#e9c9b6,#f7eee9 70%,#ffffff)}
.welcome{position:absolute;left:347px;top:519px;width:245px}
.welcome h1{font-size:20px;line-height:30px;font-weight:600;color:var(--pink-deep)}
.welcome h2{font-size:15px;line-height:25px;font-weight:600;color:var(--brown);margin-top:3px}
.welcome p{font-size:11.5px;line-height:24.5px;margin-top:7px}
.welcome a{display:block;font-size:11.5px;color:var(--blue);text-decoration:none;margin-top:6px}

.section-title{position:absolute;font-size:14.5px;font-weight:400;letter-spacing:.2px}
.title-news{color:var(--blue)}
.title-learning{color:#86a81b}
.title-creativity{color:var(--pink)}
.title-sharing{color:var(--blue)}

.news{position:absolute;left:609px;top:557px;width:245px;height:224px;background:linear-gradient(var(--cream),#fdf6d4);border-top:3px solid var(--yellow);box-shadow:1px 1px 3px rgba(0,0,0,.15);padding:18px 15px;font-size:10.5px;line-height:22px;color:#6e6e6e}

.feature-frame{position:absolute;top:856px;width:245px;height:124px;border:1px solid #e6e6e6;box-shadow:0 1px 3px rgba(0,0,0,.1);padding:4px;background:var(--white)}
.feature-frame div{width:100%;height:100%}
.frame-learning{border-bottom:3px solid var(--green)}
.frame-creativity{border-bottom:3px solid var(--pink)}
.frame-sharing{border-bottom:3px solid var(--blue-mid)}
.feature-text{position:absolute;top:997px;width:245px;font-size:11.5px;line-height:22px}

.site-footer{position:absolute;left:0;top:1084px;width:940px;height:116px;background:linear-gradient(var(--blue-mid),var(--blue));border-top:5px solid var(--green)}
.social{position:absolute;top:18px;width:42px;height:42px;border-radius:7px;background:linear-gradient(#fafafa,#d6d6d6);box-shadow:0 1px 2px rgba(0,0,0,.3)}
</style>
</head>
<body>
<header class="site-header">
  <div class="brand"><span class="brand-dot"></span><span class="brand-name">Puddle Jump Kidscare</span></div>
  <div class="search">
    <svg width="12" height="12" viewBox="0 0 12 12"><circle cx="5" cy="5" r="3.6" fill="none" stroke="#bdbdbd" stroke-width="1.6"/><line x1="7.6" y1="7.6" x2="11" y2="11" stroke="#bdbdbd" stroke-width="1.8"/></svg>
    Search
  </div>
</header>

<nav class="main-nav">
  <a class="active" style="left:86px">Home</a>
  <a style="left:163px">About Us</a>
  <a style="left:249px">Services</a>
  <a style="left:330px">Hours and Fees</a>
  <a style="left:451px">Policies</a>
  <a style="left:528px">Contact Us</a>
  <a style="left:623px">Photos</a>
  <a style="left:697px">Testimonials</a>
</nav>

<section class="hero" role="img" aria-label="Toddler in a dark jacket sitting among autumn leaves beside a tree">
  <div class="hero-caption">
    <div class="lead">a playspace where children can</div>
    <div class="big">play,</div>
    <div class="big2">create, and imagine!</div>
  </div>
  <div class="hero-arrow" style="left:8px"><svg width="12" height="12" viewBox="0 0 12 12"><path d="M6 2 2 6l4 4M10 2 6 6l4 4" fill="none" stroke="#0192cd" stroke-width="1.6"/></svg></div>
  <div class="hero-arrow" style="left:898px"><svg width="12" height="12" viewBox="0 0 12 12"><path d="M2 2l4 4-4 4M6 2l4 4-4 4" fill="none" stroke="#0192cd" stroke-width="1.6"/></svg></div>
</section>
<div class="hero-shadow"></div>

<div class="welcome-photo" role="img" aria-label="Two young children brushing their teeth"></div>
<section class="welcome">
  <h1>Welcome to Puddle Jump Kidscare,</h1>
  <h2>a playspace where children can play, create, and imagine!</h2>
  <p>Welcome to Puddle Jump Kidscare, a licensed Group Family Day Care, located in New York City's beautiful Upper East Side.</p>
  <a href="#">Read More...</a>
</section>

<h3 class="section-title title-news" style="left:609px;top:523px">LATEST NEWS</h3>
<div class="news">We are thrilled to have found a new cheerful space with a private backyard! It's large, sunny, and filled with outdoor play equipment such as a toddler slide, sand/water activity table, and lots of toys! Please stay tuned for updates on our program and services as we say goodbye to Winter and hello to Spring!</div>

<h3 class="section-title title-learning" style="left:86px;top:807px">LEARNING</h3>
<h3 class="section-title title-creativity" style="left:347px;top:807px">CREATIVITY</h3>
<h3 class="section-title title-sharing" style="left:609px;top:807px">SHARING</h3>

<div class="feature-frame frame-learning" style="left:86px"><div role="img" aria-label="Children learning together at a table" style="background:linear-gradient(90deg,#b57a4e,#f2a12a 40%,#3aa68a 75%,#2f6fa8)"></div></div>
<div class="feature-frame frame-creativity" style="left:347px"><div role="img" aria-label="Children doing colourful paper crafts" style="background:linear-gradient(90deg,#c8323a,#e58a4c 40%,#d9c7c0 70%,#b9413e)"></div></div>
<div class="feature-frame frame-sharing" style="left:609px"><div role="img" aria-label="Children drawing together with pencils" style="background:linear-gradient(90deg,#5b3a2e,#d9b9a6 45%,#e6d6cc 70%,#d8623c)"></div></div>

<p class="feature-text" style="left:87px">We develop age-appropriate activities that introduce and strengthen academic and social skills.</p>
<p class="feature-text" style="left:348px">We develop age-appropriate activities that introduce and strengthen academic and social skills.</p>
<p class="feature-text" style="left:610px">We develop age-appropriate activities that introduce and strengthen academic and social skills.</p>

<footer class="site-footer">
  <span class="social" style="left:332px"></span>
  <span class="social" style="left:379px"></span>
  <span class="social" style="left:427px"></span>
  <span class="social" style="left:474px"></span>
  <span class="social" style="left:521px"></span>
</footer>
</body>
</html>
```